Business Cards - Brightpath Horizon

need to design unique business card for my mortgage business. I need to design credit card style business card for my business or any unique idea that you might have

Target Market(s)

Home Loan customers

Industry/Entity Type

Mortgage Brokerage

Contact Information for Business Card

please design credit card style or very unique style business card

Colors

Designer to choose colors to be used in the design.

Requirements
Must have
• Name
• position
• Phone number
• fax number
• email address
• website address
• social media address
• All above fields will be provided once design in finalised

```html
<!DOCTYPE html>
<html lang="en">
<head>
<meta charset="utf-8">
<title>Brightpath Horizon – Business Card</title>
<link rel="stylesheet" href="https://fonts.googleapis.com/css2?family=Roboto:wght@400;500&family=Roboto+Condensed:wght@500;700&family=Share+Tech+Mono&display=swap">
<style>
  :root{
    --stage:#3a3a3a;
    --paper:#f3f3f3;
    --brand-blue:#1f3fc4;
    --gold:#f4cf3a;
    --gold-deep:#c99a12;
    --navy:#0d2a9c;
    --white:#ffffff;
    --grad-orange:#eaa25a;
    --grad-blue:#1a3fd8;
    --grad-cyan:#0aa8ea;
  }
  *{box-sizing:border-box;margin:0;padding:0}
  html,body{width:1200px;height:886px;overflow:hidden}
  body{background:var(--stage);position:relative;font-family:"Roboto",sans-serif}
  .card{
    position:absolute;top:273px;width:540px;height:340px;border-radius:22px;overflow:hidden;
    box-shadow:0 14px 30px rgba(0,0,0,.45);
  }
  .card--front{left:40px;background:var(--paper)}
  .card--back{
    left:620px;
    background:linear-gradient(105deg,var(--grad-orange) 0%,#9a7fa8 32%,var(--grad-blue) 50%,#1560e6 75%,var(--grad-cyan) 100%);
  }
  /* front */
  .brand{position:absolute;left:0;right:0;top:136px;display:flex;justify-content:center;align-items:center;gap:12px}
  .brand__mark{width:26px;height:26px;border-radius:50%;background:var(--brand-blue)}
  .brand__name{font-family:"Roboto",sans-serif;font-weight:500;color:var(--brand-blue);font-size:34px;line-height:1}
  .front-web{position:absolute;left:0;right:0;bottom:44px;text-align:center;font-size:11px;letter-spacing:5px;color:#444}
  /* back */
  .back-texture{position:absolute;left:0;top:0;width:230px;height:260px;
    background:radial-gradient(ellipse at 35% 40%,rgba(245,180,110,.55),rgba(245,180,110,0) 70%)}
  .edge-tab{position:absolute;width:14px;height:64px;background:var(--white);border-radius:8px}
  .edge-tab--left{left:-6px;top:196px}
  .edge-tab--right{right:-6px;top:60px}
  .social{position:absolute;right:58px;top:34px;display:flex;gap:4px}
  .social__dot{width:26px;height:26px;border-radius:50%;background:radial-gradient(circle at 35% 35%,var(--gold),var(--gold-deep));border:2px solid #fff3b0}
  .card-number{position:absolute;right:52px;top:118px;font-family:"Share Tech Mono",monospace;font-size:40px;letter-spacing:4px;color:var(--gold);text-shadow:0 1px 0 #8a6a00}
  .holder{position:absolute;right:48px;top:196px;text-align:right;font-family:"Roboto Condensed",sans-serif}
  .holder__name{font-weight:700;font-size:21px;color:var(--navy)}
  .holder__role{font-weight:500;font-size:15px;color:var(--white)}
  .back-brand{position:absolute;left:42px;top:190px;display:flex;align-items:center;gap:8px}
  .back-brand__mark{width:16px;height:16px;border-radius:50%;background:var(--white)}
  .back-brand__name{font-family:"Roboto",sans-serif;font-weight:500;color:var(--white);font-size:22px;line-height:1}
  .contact{position:absolute;left:42px;bottom:30px;font-size:13px;line-height:1.45;color:var(--white)}
  .contact b{font-weight:500}
</style>
</head>
<body>
  <section class="card card--front">
    <div class="brand">
      <span class="brand__mark"></span>
      <p class="brand__name">Brightpath Horizon</p>
    </div>
    <p class="front-web">www.brightpathhorizon.com</p>
  </section>

  <section class="card card--back">
    <div class="back-texture" role="img" aria-label="Faint tree and house illustration fading into the orange corner"></div>
    <span class="edge-tab edge-tab--left"></span>
    <span class="edge-tab edge-tab--right"></span>
    <div class="social" aria-label="Social media links">
      <span class="social__dot"></span><span class="social__dot"></span><span class="social__dot"></span><span class="social__dot"></span>
    </div>
    <p class="card-number">731 562 0498</p>
    <div class="holder">
      <p class="holder__name">DANIEL REYES</p>
      <p class="holder__role">CEO/FOUNDER</p>
    </div>
    <div class="back-brand">
      <span class="back-brand__mark"></span>
      <p class="back-brand__name">Brightpath Horizon</p>
    </div>
    <div class="contact">
      <p><b>F:</b> 614 205 3871</p>
      <p><b>E:</b> daniel@brightpathhorizon.com</p>
      <p><b>W:</b> www.brightpathhorizon.com</p>
    </div>
  </section>
</body>
</html>
```